RW Framewell Inc Business cards

We need business cards using our existing logo but slightly modified. Right now the logo says RW Loadbearing Masonry. We want to keep the RW part of the design, but replace the Structural Concrete portion with "FRAMEWELL". Please see the attached file.
Ideally this would be a blank template so we can add Different Names, titles, and phone numbers later.
On the one side we want only the logo and on the other side the detail. I'm attaching an example for you to see.
Please reach out with any other questions. Our address and other details will be given out once we find a design we like.

Target Market(s)

Construction Industry

```html
<!DOCTYPE html>
<html lang="en">
<head>
<meta charset="utf-8">
<title>RW Framewell Inc — Business Cards</title>
<link rel="stylesheet" href="https://fonts.googleapis.com/css2?family=Michroma&family=Arimo:wght@400&display=swap">
<style>
  :root {
    --backdrop: #1f1f1f;
    --brand-blue: #1e75bd;
    --steel-grey: #818284;
    --text-grey: #7a7b7d;
    --paper: #ffffff;
    --rule: #c9c9c9;
  }
  * { margin: 0; padding: 0; box-sizing: border-box; }
  html, body {
    width: 1200px; height: 1015px; overflow: hidden;
    background: var(--backdrop);
  }
  .canvas {
    position: relative; width: 1200px; height: 1015px;
  }
  .card {
    position: absolute; left: 320px; width: 560px; height: 320px;
    overflow: hidden;
    box-shadow: 0 14px 30px rgba(0,0,0,.55);
  }

  /* Logo side */
  .card-front { top: 140px; background: var(--brand-blue); }
  .card-front .lower-band {
    position: absolute; left: 0; right: 0; bottom: 0; height: 112px;
    background: var(--steel-grey);
  }
  .card-front .wordmark {
    position: absolute; left: 0; right: 0; top: 120px;
    text-align: center;
    font-family: "Michroma", sans-serif; font-size: 40px; letter-spacing: 2px;
    color: var(--paper);
    white-space: nowrap;
  }

  /* Detail side */
  .card-back { top: 530px; background: var(--paper); }
  .logo-lockup {
    position: absolute; left: 28px; top: 138px;
    width: 248px;
    display: flex; align-items: center; gap: 8px;
  }
  .logo-lockup .mark-square {
    width: 18px; height: 18px; background: var(--brand-blue); flex: none;
  }
  .logo-lockup .company-name {
    font-family: "Michroma", sans-serif; font-size: 15px; letter-spacing: .5px;
    color: var(--brand-blue);
    white-space: nowrap;
  }
  .divider {
    position: absolute; left: 292px; top: 80px; width: 1px; height: 140px;
    background: var(--rule);
  }
  .contact {
    position: absolute; left: 316px; top: 88px; width: 230px;
    font-family: "Arimo", sans-serif; color: var(--text-grey);
  }
  .contact .person-name {
    font-family: "Michroma", sans-serif; font-size: 15px; letter-spacing: .5px;
    color: var(--brand-blue);
    white-space: nowrap;
  }
  .contact .person-title { font-size: 13px; margin-top: 2px; }
  .contact ul { list-style: none; margin-top: 16px; }
  .contact li {
    display: flex; align-items: center; gap: 8px;
    font-size: 13px; line-height: 21px;
    white-space: nowrap;
  }
  .contact li svg { width: 14px; height: 14px; fill: var(--brand-blue); flex: none; }
  .contact .web-highlight { color: var(--brand-blue); }
  .footer-blue {
    position: absolute; left: 0; bottom: 0; width: 370px; height: 14px;
    background: var(--brand-blue);
  }
  .footer-grey {
    position: absolute; right: 0; bottom: 0; width: 186px; height: 30px;
    background: var(--steel-grey);
  }
</style>
</head>
<body>
<main class="canvas">

  <section class="card card-front" aria-label="Business card, logo side">
    <div class="lower-band"></div>
    <div class="wordmark">RW FRAMEWELL</div>
  </section>

  <section class="card card-back" aria-label="Business card, detail side">
    <div class="logo-lockup">
      <span class="mark-square"></span>
      <span class="company-name">RW FRAMEWELL</span>
    </div>
    <div class="divider"></div>
    <div class="contact">
      <p class="person-name">DANIEL HARTLEY</p>
      <p class="person-title">Managing Director</p>
      <ul>
        <li>
          <svg viewBox="0 0 24 24" aria-hidden="true"><path d="M6.6 10.8a15.1 15.1 0 0 0 6.6 6.6l2.2-2.2c.3-.3.7-.4 1-.2 1.1.4 2.3.6 3.6.6.6 0 1 .4 1 1V20c0 .6-.4 1-1 1A17 17 0 0 1 3 4c0-.6.4-1 1-1h3.5c.6 0 1 .4 1 1 0 1.3.2 2.5.6 3.6.1.3 0 .7-.2 1z"/></svg>
          044-987 650 312
        </li>
        <li>
          <svg viewBox="0 0 24 24" aria-hidden="true"><path d="M2 5h20v14H2z M2 5l10 8 10-8" stroke="#fff" stroke-width="1.5"/></svg>
          hello@framewellmail.com
        </li>
        <li>
          <svg viewBox="0 0 24 24" aria-hidden="true"><circle cx="12" cy="12" r="10"/><path d="M2 12h20M12 2c3 3 3 17 0 20M12 2c-3 3-3 17 0 20" stroke="#fff" stroke-width="1.3" fill="none"/></svg>
          <span>www.<span class="web-highlight">rwframewell</span>.com</span>
        </li>
      </ul>
    </div>
    <div class="footer-blue"></div>
    <div class="footer-grey"></div>
  </section>

</main>
</body>
</html>
```